High-end construction company needs a business card design

We need a modern looking business card that draws people in, is memorable and looks so good people will want to sick it on their fridges.
On the first side what is needed are:
Logo
My name - Tomasz Brelwik
Title - Managing Director
Website - www.varkelt.co.uk
Email - tomasz@varkelt.co.uk
Telephone - 020 5194 6281
Mobile - 07845139072
On the back side was is needed is a list of all the services we provide:
-Kitchen Renovations
-Bathroom Renovations
-House Renovations
-Garage Conversions
-Extensions
-Loft Conversions
-Conservatories
-Carpentry
-Tiling
-Electrical
-Plumbing & Heating
-Bricklaying
-Landscaping
-Decorating
-Plastering
We would like the colours to be the same shades as on the logo with grey or black for the words.
Target Market(s)
Anyone who needs building work done
Contact Information for Business Card
This business card is for a construction company which strives to deliver excellent service and quality.
The look and feel of the card should represent this.
Requirements
Must have
- On the first side what is needed are:
Logo
My name - Tomasz Brelwik
Title - Managing Director
Website - www.varkelt.co.uk
Email - tomasz@varkelt.co.uk
Telephone - 020 5194 6281
Mobile - 07845139072
Nice to have
- Cool looking features

```html
<!DOCTYPE html>
<html lang="en">
<head>
<meta charset="utf-8">
<title>Varkelt Construction Ltd – Business Card</title>
<link rel="stylesheet" href="https://fonts.googleapis.com/css2?family=Roboto:wght@400;900&display=swap">
<style>
  :root {
    --backdrop: #000000;
    --card: #2f3033;
    --card-edge: #38393c;
    --green: #6cc04a;
    --text-light: #ffffff;
    --text-muted: #c9c9c9;
    --divider: #55575a;
  }
  * { box-sizing: border-box; margin: 0; padding: 0; }
  html, body {
    width: 1200px; height: 900px; overflow: hidden;
    background: var(--backdrop);
    font-family: "Roboto", Arial, sans-serif;
  }
  .canvas { position: relative; width: 1200px; height: 900px; }

  .card {
    position: absolute;
    width: 458px; height: 282px;
    border-radius: 13px;
    background: linear-gradient(180deg, var(--card-edge) 0%, var(--card) 100%);
  }
  .card--front { left: 138px; top: 265px; }
  .card--back  { left: 625px; top: 268px; }

  /* Front */
  .brand {
    position: absolute; left: 24px; top: 150px;
    width: 198px;
    color: var(--green); font-weight: 900;
    text-transform: uppercase;
  }
  .brand__name { display: block; font-size: 46px; line-height: 1; letter-spacing: 0; }
  .brand__sub  { display: block; font-size: 12.4px; letter-spacing: 1.6px; margin-top: 4px; }

  .divider {
    position: absolute; left: 243px; top: 81px;
    width: 1px; height: 121px; background: var(--divider);
  }

  .person { position: absolute; left: 263px; top: 78px; }
  .person__name {
    color: var(--green); font-weight: 900;
    font-size: 18px; text-transform: uppercase; line-height: 1.1;
  }
  .person__title { color: var(--text-light); font-size: 14px; line-height: 1.2; }

  .contacts { position: absolute; left: 263px; top: 136px; list-style: none; }
  .contacts li {
    display: flex; align-items: center; gap: 5px;
    color: var(--text-light); font-size: 13.4px; height: 16.6px;
  }
  .contacts svg { width: 13px; height: 13px; flex: none; }

  /* Back */
  .services {
    position: absolute; top: 66px; list-style: none;
  }
  .services--left  { left: 27px; }
  .services--right { left: 270px; }
  .services li {
    position: relative; padding-left: 14px;
    color: var(--text-muted); font-size: 14px;
    text-transform: uppercase; height: 20.4px; line-height: 20.4px;
    letter-spacing: 0.2px;
  }
  .services li::before {
    content: ""; position: absolute; left: 0; top: 7.5px;
    width: 6px; height: 6px; border-radius: 50%; background: var(--green);
  }
</style>
</head>
<body>
<div class="canvas">

  <section class="card card--front">
    <div class="brand">
      <span class="brand__name">Varkelt</span>
      <span class="brand__sub">Construction Ltd</span>
    </div>

    <div class="divider"></div>

    <div class="person">
      <p class="person__name">Tomasz Brelwik</p>
      <p class="person__title">Managing Director</p>
    </div>

    <ul class="contacts">
      <li>
        <svg viewBox="0 0 16 16" aria-hidden="true"><path d="M4 1.5l2.2 3-1.3 1.4c.8 1.9 2.3 3.4 4.2 4.2l1.4-1.3 3 2.2-1.2 2.5C7.5 13.3 2.7 8.5 1.5 3.7z" fill="none" stroke="var(--green)" stroke-width="1.4" stroke-linejoin="round"/></svg>
        020 5194 6281
      </li>
      <li>
        <svg viewBox="0 0 16 16" aria-hidden="true"><rect x="4" y="1" width="8" height="14" rx="1.5" fill="none" stroke="var(--green)" stroke-width="1.6"/><rect x="5.5" y="3" width="5" height="8" fill="var(--green)"/></svg>
        07845139072
      </li>
      <li>
        <svg viewBox="0 0 16 16" aria-hidden="true"><rect x="1" y="3" width="14" height="10" fill="var(--green)"/><path d="M1 3l7 6 7-6" fill="none" stroke="var(--card)" stroke-width="1.2"/></svg>
        tomasz@varkelt.co.uk
      </li>
      <li>
        <svg viewBox="0 0 16 16" aria-hidden="true"><g fill="none" stroke="var(--green)" stroke-width="1.2"><circle cx="8" cy="8" r="6.5"/><ellipse cx="8" cy="8" rx="3" ry="6.5"/><path d="M1.5 8h13M2.5 5h11M2.5 11h11"/></g></svg>
        www.varkelt.co.uk
      </li>
    </ul>
  </section>

  <section class="card card--back">
    <ul class="services services--left">
      <li>Kitchen Renovations</li>
      <li>Bathroom Renovations</li>
      <li>House Renovations</li>
      <li>Garage Conversions</li>
      <li>Extensions</li>
      <li>Loft Conversions</li>
      <li>Conservatories</li>
      <li>Carpentry</li>
    </ul>
    <ul class="services services--right">
      <li>Tiling</li>
      <li>Electrical</li>
      <li>Plumbing &amp; Heating</li>
      <li>Bricklaying</li>
      <li>Landscaping</li>
      <li>Decorating</li>
      <li>Plastering</li>
    </ul>
  </section>

</div>
</body>
</html>
```